New Design for Willow Glow & Laser

The name of our company is Willow Glow & Laser, and this is our current website: www.WillowGlowLaser.example. We are looking for a fresh design mock-up of our website.
What is important to us?
> We want to maintain the same navigation.
> We want to use the same content (e.g., text, pictures, etc.)
> We want to maintain the color scheme.
> The website aims to get visitors to BOOK ONLINE or BUY ONLINE.
Essential instructions for designers:
> Please visit our current website and our social media accounts to get a better idea of our brand design.
> We want a mockup design for our home page, service page, pricing page, before & after page, shop deals page, careers page, contact pages, and blog pages.
> Color codes: #faa641, #222222, #fffffe, #ea8103
Target Market(s)
women 25 - 45
Number of Pages Required
5+ page

```html
<!DOCTYPE html>
<html lang="en">
<head>
<meta charset="utf-8">
<title>Willow Glow &amp; Laser — Home</title>
<link href="https://fonts.googleapis.com/css2?family=Outfit:wght@400;500;600;700&display=swap" rel="stylesheet">
<style>
:root{
  --orange:#faa641;
  --orange-deep:#ea8103;
  --ink:#222222;
  --white:#fffffe;
  --cream:#fff3e5;
  --body:#3a3a3a;
}
*{box-sizing:border-box;margin:0;padding:0}
html,body{width:1200px;height:3192px;overflow:hidden;background:var(--white);font-family:'Outfit',sans-serif;color:var(--ink)}
.page{position:relative;width:1200px;height:3192px}
.abs{position:absolute}
.btn{position:absolute;display:flex;align-items:center;justify-content:center;height:34px;border-radius:17px;font-size:12px;font-weight:500;white-space:nowrap}
.btn-outline{border:1px solid var(--orange-deep);color:var(--orange-deep);background:var(--white)}
.btn-solid{background:var(--orange);color:var(--white)}
.btn-white{background:var(--white);color:var(--orange-deep)}
.ph{position:absolute;border-radius:10px;overflow:hidden}
.accent{color:var(--orange)}
.mark{display:inline-block;width:18px;height:18px;border-radius:50%;background:var(--orange)}
.eyebrow{position:absolute;display:flex;align-items:center;gap:8px}
.eyebrow .rule{width:60px;height:1px;background:var(--orange)}

/* header */
.header{position:absolute;top:0;left:0;width:1200px;height:70px;background:var(--white)}
.brand{position:absolute;left:148px;top:16px;display:flex;align-items:center;gap:8px}
.brand-name{font-weight:700;font-size:19px;line-height:1;letter-spacing:1px;color:var(--ink)}
.brand-name small{display:block;font-size:10px;letter-spacing:3px;margin-top:4px}
.nav{position:absolute;left:405px;top:28px;display:flex;gap:28px;font-size:12.5px;font-weight:500}
.nav .active{color:var(--orange-deep)}

/* hero */
.hero{position:absolute;top:70px;left:0;width:1200px;height:474px;
  background:
    linear-gradient(90deg,rgba(20,16,14,.78) 0%,rgba(20,16,14,.45) 35%,rgba(20,16,14,0) 60%),
    radial-gradient(ellipse 170px 200px at 590px 130px,#c99b7e 0%,rgba(201,155,126,0) 100%),
    radial-gradient(ellipse 170px 200px at 890px 120px,#d4a588 0%,rgba(212,165,136,0) 100%),
    radial-gradient(ellipse 260px 260px at 560px 420px,#3f6470 0%,rgba(63,100,112,0) 100%),
    radial-gradient(ellipse 300px 260px at 930px 440px,#c9b6a4 0%,rgba(201,182,164,0) 100%),
    radial-gradient(ellipse 160px 220px at 1150px 230px,#3d5a2c 0%,rgba(61,90,44,0) 100%),
    linear-gradient(100deg,#5a5048 0%,#8a7a6c 50%,#a8998a 80%,#7e705f 100%)}
.hero h1{position:absolute;left:141px;top:128px;font-size:56px;font-weight:600;line-height:64px;color:var(--white)}
.hero p{position:absolute;left:141px;top:272px;font-size:15px;line-height:25px;color:var(--white)}
.scroll{position:absolute;left:572px;top:516px;width:56px;height:56px;border-radius:50%;background:var(--white);box-shadow:0 4px 14px rgba(0,0,0,.12);display:flex;align-items:center;justify-content:center}

/* about */
.h2{position:absolute;font-size:28px;font-weight:600;line-height:36px}
.about p{position:absolute;left:613px;width:432px;font-size:11.5px;line-height:22.5px;color:var(--body)}

/* offer */
.offer{position:absolute;top:1115px;left:0;width:1200px;height:490px;background:var(--cream)}
.card-img{position:absolute;top:151px;width:167px;height:181px;border-radius:8px}
.card-label{position:absolute;top:353px;font-size:14px;font-weight:500;line-height:20px}

/* testimonial */
.testi{position:absolute;left:268px;top:1690px;width:790px;height:350px;border-radius:24px;background:var(--ink)}

/* cta */
.cta{position:absolute;left:141px;top:2528px;width:917px;height:245px;border-radius:24px;background:var(--orange);text-align:center}

/* footer */
.footer{position:absolute;left:0;top:2858px;width:1200px;height:334px;background:var(--ink);color:var(--white)}
.footer h4{position:absolute;top:66px;font-size:14px;font-weight:600;color:var(--orange)}
.footer ul{position:absolute;top:100px;list-style:none;font-size:12px;line-height:28px}
.footer .info{position:absolute;font-size:12px;line-height:16px;display:flex;gap:10px}
.social{position:absolute;top:3151px;width:24px;height:24px;border-radius:50%;background:var(--orange)}
</style>
</head>
<body>
<div class="page">

  <header class="header">
    <div class="brand"><span class="mark" style="width:26px;height:26px"></span><div class="brand-name">WILLOW GLOW<small>&amp; LASER</small></div></div>
    <nav class="nav">
      <span class="active">Home</span><span>Services ⌄</span><span>Pricing ⌄</span><span>About ⌄</span><span>Blog</span><span>Contact</span>
    </nav>
    <div class="btn btn-outline" style="left:840px;top:18px;width:106px">Book Online</div>
    <div class="btn btn-solid" style="left:960px;top:18px;width:98px">Buy Online</div>
  </header>

  <section class="hero" role="img" aria-label="Photo of two smiling women holding gift cards">
    <h1>Your Skin <span class="mark" style="width:40px;height:40px;vertical-align:-4px"></span><br><span class="accent">Deserves</span> It</h1>
    <p>LASER CENTER &amp; MEDISPA located in Downtown<br>Phoenix, Tempe, Tucson, &amp; Yuma.</p>
    <div class="btn btn-white" style="left:141px;top:345px;width:106px">Book Online</div>
    <div class="btn btn-solid" style="left:261px;top:345px;width:100px">Buy Online</div>
  </section>
  <div class="scroll"><svg width="24" height="30" viewBox="0 0 24 30"><rect x="2" y="2" width="20" height="26" rx="10" fill="none" stroke="#faa641" stroke-width="1.8"/><path d="M12 9v11M8 16l4 4 4-4" fill="none" stroke="#faa641" stroke-width="1.8"/></svg></div>

  <section class="about">
    <div class="abs" style="left:141px;top:650px;width:82px;height:82px;border-radius:50%;background:#fdd9a8"></div>
    <div class="ph" role="img" aria-label="Photo of a specialist treating a client's lips" style="left:180px;top:688px;width:303px;height:324px;background:radial-gradient(ellipse 90px 110px at 90px 140px,#d9b49a 0%,rgba(217,180,154,0) 100%),radial-gradient(ellipse 80px 100px at 240px 90px,#e2c0a6 0%,rgba(226,192,166,0) 100%),radial-gradient(ellipse 110px 140px at 230px 260px,#2a2523 0%,rgba(42,37,35,0) 100%),linear-gradient(135deg,#e8e4df 0%,#cfc7bf 55%,#8d8178 100%)"></div>
    <div class="ph" role="img" aria-label="Photo of a woman checking her skin in a hand mirror" style="left:400px;top:885px;width:153px;height:145px;background:radial-gradient(ellipse 40px 50px at 55px 60px,#c79d84 0%,rgba(199,157,132,0) 100%),radial-gradient(ellipse 40px 60px at 120px 40px,#2b2725 0%,rgba(43,39,37,0) 100%),linear-gradient(135deg,#ece9e6,#b9b0aa);border:3px solid var(--white)"></div>
    <div class="eyebrow" style="left:613px;top:678px"><span class="mark"></span><span class="rule"></span></div>
    <h2 class="h2" style="left:613px;top:712px">About Willow Glow &amp; <span class="accent">Laser</span></h2>
    <p style="top:773px">At Willow Glow &amp; Laser, we’ve always believed that caring about your skin and your appearance is not selfish, it is self-care. It’s time to be proud of the steps you take to look your best and it’s time you ask for the best. Your skin deserves it.</p>
    <p style="top:870px">Willow brings to you the latest technology, techniques, and the best professionals to deliver the results you want guaranteed.</p>
    <p style="top:923px">It’s time to cross out the judgment, the labels, the hesitation, and the regrets. We offer clinic locations in Tucson, AZ, Phoenix, AZ, Tempe, AZ and Yuma, AZ.</p>
    <div class="btn btn-solid" style="left:613px;top:992px;width:106px;background:var(--orange-deep)">Book Online</div>
  </section>

  <section class="offer">
    <div class="eyebrow" style="left:522px;top:46px"><span class="rule"></span><span class="mark"></span><span class="rule"></span></div>
    <h2 class="h2" style="left:0;width:1200px;text-align:center;top:80px">What We <span class="accent">Offer</span></h2>
    <div class="card-img" role="img" aria-label="Photofacial treatment photo" style="left:141px;background:radial-gradient(ellipse 70px 80px at 90px 100px,#e8b99a 0%,rgba(232,185,154,0) 100%),radial-gradient(ellipse 50px 60px at 30px 60px,#e7e4e1 0%,rgba(231,228,225,0) 100%),linear-gradient(135deg,#bcaea4,#5e504a)"></div>
    <div class="card-img" role="img" aria-label="Botox injection close-up photo" style="left:329px;background:radial-gradient(ellipse 100px 110px at 70px 90px,#e2b89c 0%,rgba(226,184,156,0) 100%),radial-gradient(ellipse 40px 80px at 150px 60px,#5a3a2a 0%,rgba(90,58,42,0) 100%),linear-gradient(135deg,#d8b59b,#9b735c)"></div>
    <div class="card-img" role="img" aria-label="Laser hair removal photo" style="left:516px;background:radial-gradient(ellipse 70px 60px at 90px 60px,#d6a88e 0%,rgba(214,168,142,0) 100%),radial-gradient(ellipse 40px 40px at 30px 130px,#f2f1f0 0%,rgba(242,241,240,0) 100%),radial-gradient(ellipse 60px 80px at 150px 40px,#1f1c1b 0%,rgba(31,28,27,0) 100%),linear-gradient(135deg,#a7a09c,#3c3634)"></div>
    <div class="card-img" role="img" aria-label="Facial and peel treatment photo" style="left:704px;background:radial-gradient(ellipse 60px 70px at 110px 50px,#262220 0%,rgba(38,34,32,0) 100%),radial-gradient(ellipse 50px 40px at 60px 130px,#d6ae97 0%,rgba(214,174,151,0) 100%),linear-gradient(135deg,#ecebea,#a69d98)"></div>
    <div class="card-img" role="img" aria-label="Lip enhancement treatment photo" style="left:892px;background:radial-gradient(ellipse 60px 80px at 130px 100px,#e2b3a0 0%,rgba(226,179,160,0) 100%),radial-gradient(ellipse 80px 110px at 40px 90px,#1b1918 0%,rgba(27,25,24,0) 100%),linear-gradient(135deg,#cfc9c6,#463c38)"></div>
    <div class="card-label" style="left:141px">Photofacials →</div>
    <div class="card-label" style="left:329px">Botox Injections →</div>
    <div class="card-label" style="left:516px">Laser Hair Removal →</div>
    <div class="card-label" style="left:704px">Facials &amp; Peels →</div>
    <div class="card-label" style="left:892px">Lip Shape &amp;<br>Enhancement →</div>
    <div class="btn btn-outline" style="left:491px;top:415px;width:106px">Book Online</div>
    <div class="btn btn-solid" style="left:611px;top:415px;width:99px">Buy Online</div>
  </section>

  <section class="testi">
    <div class="eyebrow" style="left:192px;top:30px"><span class="mark"></span><span class="rule"></span></div>
    <h2 class="h2" style="left:192px;top:62px;color:var(--white)">What Our Happy<br><span class="accent">Clients Say</span></h2>
    <p class="abs" style="left:192px;top:160px;width:540px;font-size:12.5px;line-height:25px;color:var(--white)">"Lena is my technician and I love her! Always goes the extra mile to make sure areas are covered, and that I'm getting the best result. I couldn't be happier."</p>
    <div class="abs" style="left:191px;top:224px;color:var(--orange);font-size:17px;letter-spacing:2px">★★★★★</div>
    <div class="abs" style="left:192px;top:256px;font-size:17px;font-weight:600;color:var(--white)">Maya R.</div>
    <svg class="abs" style="left:190px;top:304px" width="80" height="14" viewBox="0 0 80 14"><path d="M26 7H2M8 1L2 7l6 6M54 7h24M72 1l6 6-6 6" fill="none" stroke="#faa641" stroke-width="1.6"/></svg>
  </section>
  <div class="ph" role="img" aria-label="Portrait photo of a smiling client" style="left:141px;top:1725px;width:262px;height:280px;background:radial-gradient(ellipse 70px 90px at 130px 120px,#e4b69c 0%,rgba(228,182,156,0) 100%),radial-gradient(ellipse 130px 70px at 130px 270px,#a11e26 0%,rgba(161,30,38,0) 100%),radial-gradient(ellipse 120px 150px at 130px 110px,#2c201c 0%,rgba(44,32,28,0) 100%),linear-gradient(135deg,#c9b8a6,#8d7a68)"></div>

  <section class="gallery">
    <div class="ph" role="img" aria-label="Clinic photo: specialist treating a client" style="left:-10px;top:2172px;width:223px;height:193px;background:radial-gradient(ellipse 70px 80px at 70px 90px,#1e1b1a 0%,rgba(30,27,26,0) 100%),radial-gradient(ellipse 50px 40px at 160px 150px,#d3a690 0%,rgba(211,166,144,0) 100%),linear-gradient(135deg,#e4e1de,#8b827d)"></div>
    <div class="ph" role="img" aria-label="Clinic photo: consultation with tablet" style="left:235px;top:2140px;width:230px;height:117px;background:radial-gradient(ellipse 50px 60px at 60px 70px,#1f1c1b 0%,rgba(31,28,27,0) 100%),radial-gradient(ellipse 50px 60px at 180px 70px,#2a2422 0%,rgba(42,36,34,0) 100%),linear-gradient(135deg,#ece6df,#b8a898)"></div>
    <div class="ph" role="img" aria-label="Clinic photo: client with hand mirror" style="left:235px;top:2278px;width:230px;height:143px;background:radial-gradient(ellipse 40px 55px at 60px 60px,#1c1a19 0%,rgba(28,26,25,0) 100%),radial-gradient(ellipse 50px 60px at 150px 70px,#c99c82 0%,rgba(201,156,130,0) 100%),linear-gradient(135deg,#ebe8e6,#9d948f)"></div>
    <div class="ph" role="img" aria-label="Clinic photo: two staff holding gift cards" style="left:485px;top:2140px;width:230px;height:302px;background:radial-gradient(ellipse 45px 55px at 65px 80px,#cf9f84 0%,rgba(207,159,132,0) 100%),radial-gradient(ellipse 45px 55px at 170px 80px,#d8ab90 0%,rgba(216,171,144,0) 100%),radial-gradient(ellipse 60px 110px at 65px 220px,#34495a 0%,rgba(52,73,90,0) 100%),radial-gradient(ellipse 40px 40px at 115px 240px,#f4c56a 0%,rgba(244,197,106,0) 100%),linear-gradient(135deg,#d9d4cf,#8a7b70)"></div>
    <div class="ph" role="img" aria-label="Clinic photo: skin close-up" style="left:736px;top:2140px;width:230px;height:150px;background:radial-gradient(ellipse 120px 90px at 120px 90px,#d9ab94 0%,rgba(217,171,148,0) 100%),radial-gradient(ellipse 60px 80px at 30px 30px,#2b211d 0%,rgba(43,33,29,0) 100%),linear-gradient(135deg,#c99a83,#8b6656)"></div>
    <div class="ph" role="img" aria-label="Clinic photo: treatment session" style="left:736px;top:2310px;width:230px;height:110px;background:radial-gradient(ellipse 50px 55px at 60px 50px,#c8a27a 0%,rgba(200,162,122,0) 100%),radial-gradient(ellipse 60px 50px at 130px 80px,#1e1b1a 0%,rgba(30,27,26,0) 100%),linear-gradient(135deg,#ece9e6,#a89f9a)"></div>
    <div class="ph" role="img" aria-label="Clinic photo: facial treatment with plant" style="left:987px;top:2190px;width:223px;height:177px;background:radial-gradient(ellipse 60px 70px at 80px 60px,#d2a78d 0%,rgba(210,167,141,0) 100%),radial-gradient(ellipse 60px 80px at 180px 40px,#4f6b3a 0%,rgba(79,107,58,0) 100%),radial-gradient(ellipse 60px 50px at 170px 130px,#d8b29c 0%,rgba(216,178,156,0) 100%),linear-gradient(135deg,#ecebe8,#8c8680)"></div>
  </section>

  <section class="cta">
    <div class="eyebrow" style="left:381px;top:40px"><span class="rule" style="background:var(--white)"></span><span class="mark" style="background:var(--white)"></span><span class="rule" style="background:var(--white)"></span></div>
    <h2 class="h2" style="left:0;width:917px;top:72px;font-size:32px;line-height:41px">If You Have Any Question,<br>Please <span style="color:var(--white)">Contact Us.</span></h2>
    <div class="btn btn-white" style="left:405px;top:180px;width:108px">Get In Touch</div>
  </section>

  <footer class="footer">
    <div class="brand" style="left:141px;top:72px"><span class="mark" style="width:34px;height:34px"></span><div class="brand-name" style="color:var(--white);font-size:26px">WILLOW GLOW<small style="font-size:12px">&amp; LASER</small></div></div>
    <p class="abs" style="left:141px;top:146px;font-size:12px;line-height:22px">Medical Director: Dr. Elena Marsh, NMD License<br>#07-2281 Contact: md@willowglowlaser.example</p>
    <h4 style="left:514px">Quick Links</h4>
    <ul style="left:514px"><li>Home</li><li>Services</li><li>Pricing</li><li>About</li><li>Blog</li></ul>
    <h4 style="left:671px">About</h4>
    <ul style="left:671px"><li>Contact</li><li>Terms &amp; Condition</li><li>Privacy Policy</li></ul>
    <h4 style="left:852px">Get In Touch</h4>
    <div class="info" style="left:852px;top:100px"><svg width="16" height="18" viewBox="0 0 16 18"><path d="M8 1a5.5 5.5 0 0 0-5.5 5.5C2.5 11 8 16 8 16s5.5-5 5.5-9.5A5.5 5.5 0 0 0 8 1z" fill="none" stroke="#faa641" stroke-width="1.6"/><circle cx="8" cy="6.5" r="2" fill="#faa641"/></svg><span>2240 North 9th Avenue Suite 310<br>Phoenix, AZ 85007</span></div>
    <div class="info" style="left:852px;top:150px"><svg width="16" height="12" viewBox="0 0 16 12"><rect width="16" height="12" rx="1.5" fill="#faa641"/><path d="M1 1.5l7 5 7-5" fill="none" stroke="#222" stroke-width="1.2"/></svg><span>hello@willowglowlaser.example</span></div>
    <div class="info" style="left:852px;top:182px"><svg width="14" height="14" viewBox="0 0 24 24"><path d="M6.6 10.8a15 15 0 0 0 6.6 6.6l2.2-2.2a1 1 0 0 1 1-.25 11.4 11.4 0 0 0 3.6.57 1 1 0 0 1 1 1V20a1 1 0 0 1-1 1A17 17 0 0 1 3 4a1 1 0 0 1 1-1h3.5a1 1 0 0 1 1 1c0 1.25.2 2.45.57 3.57a1 1 0 0 1-.25 1z" fill="#faa641"/></svg><span>(602) 555-0148</span></div>
    <div class="abs" style="left:141px;top:278px;width:917px;height:1px;background:#444"></div>
    <p class="abs" style="left:141px;top:302px;font-size:12px">© 2024 Willow Glow &amp; Laser. All Rights Reserved.</p>
  </footer>
  <div class="social" style="left:962px"></div>
  <div class="social" style="left:998px"></div>
  <div class="social" style="left:1034px"></div>

</div>
</body>
</html>
```